Need a Wordpress website for my HVAC company

I need a Wordpress website created for an HVAC company in a competitive market.
Following are some websites I like:
My current website is www.borvicoheating.com - we also have a facebook page with some pictures

We are an airconditioning and heating company that does both residential and commmercial work.
We need the following info on our website:
-mobile friendly
-Schedule an appt -repair/maintnenace/installation (i would like this option to always be on the page even if they scroll down.)
-24 hour service
-coupons /promotions
-financing
-reviews/testimonials
-about
-blog
-Our service area
The following are services we provide:
-Air conditioning - Installation/Service/Maintenance/new construction
-Heating - Installation/Service/Maintenance/new construction ( gas furnace, 2 stage furnace, electric heat)
-Duct - Repair/Replacement/Istallation - (zone systems)
-thermostats (wifi)
-Heat pump
-Air handler
-self communicating systems
-carbon monoxide testing
-hail damage
-duct sealing
-insulation
-Air cleaners - UV Air purifiers
-humidifiers

I would also like Quilbo SEO add on

Target Market(s)

Anyone who needs our services HVAC contractor

Industry/Entity Type

Hvac

Contact Information for Business Card

Phone:480-555-2046
website:www.borvicoheating.com
email pmarsh@borvicoheating.com

Coding

Coded - Design and coding required

Number of Pages Required

5+ page

Font styles to use
Serif
Sans Serif

Requirements
Must have
• I wrote in brief. I already have Webly Nest. Long story I paid for 3 years already. I need someone to put website there. Ive never used Wordpress but would like a template page so I can easily add services.
Nice to have
• Clean, bright, original

```html
<!DOCTYPE html>
<html lang="en">
<head>
<meta charset="utf-8">
<title>Borvico Heating Services – Air Conditioning and Heating</title>
<link rel="stylesheet" href="https://fonts.googleapis.com/css2?family=Open+Sans:wght@400;600;700&family=Roboto+Slab:wght@300;400&display=swap">
<style>
:root{
  --blue:#1a5b9e;
  --blue-dark:#174f8a;
  --link:#1e8fd0;
  --text:#555;
  --text-dark:#333;
  --hero-bg:#ebebeb;
  --service-bg:#c8d9e7;
  --blog-bg:#f5f5f5;
  --line:#d0d0d0;
  --white:#fff;
}
*{box-sizing:border-box;margin:0;padding:0}
html,body{width:1200px;height:2667px;overflow:hidden;background:var(--white)}
body{position:relative;font-family:"Open Sans",Arial,sans-serif;color:var(--text)}
.abs{position:absolute}
.serif{font-family:"Roboto Slab",Georgia,serif}

/* header */
.brand{left:100px;top:24px;width:130px;height:56px;display:flex;align-items:center;gap:8px}
.brand-mark{width:14px;height:14px;border-radius:50%;background:var(--blue);flex:none}
.brand-name{font-weight:700;font-size:17px;color:var(--blue)}
.top-contact{top:14px;left:630px;display:flex;align-items:center;gap:12px;font-size:13px;color:var(--text-dark)}
.top-contact .item{display:flex;align-items:center;gap:8px;margin-right:8px}
.round-ico{width:30px;height:30px;border:1px solid var(--line);border-radius:50%;display:flex;align-items:center;justify-content:center}
.login{left:1017px;top:13px;width:86px;height:31px;border:1px solid #bbb;border-radius:6px;font-size:12px;font-weight:600;color:var(--text-dark);display:flex;align-items:center;justify-content:center;gap:5px}
.nav{top:64px;left:430px;display:flex;font-size:13px;color:#555}
.nav a{text-decoration:none;color:inherit;margin-right:30px}
.nav a.active{color:var(--blue)}

/* hero */
.hero{left:0;top:100px;width:1200px;height:517px;background:var(--hero-bg)}
.van{left:100px;top:140px;width:400px;height:410px;background:linear-gradient(180deg,#f4f4f4 0%,#c9d6e6 45%,#2c4f86 100%);border-radius:18px}
.hero-title{left:587px;top:160px;font-size:32px;color:#555;font-weight:400}
.hero-title b{color:var(--blue);font-weight:700}
.hero-sub{left:587px;top:216px;font-size:20px;color:var(--text-dark)}
.btn-schedule{left:587px;top:270px;width:218px;height:47px;border:1px solid #aaa;border-radius:5px;font-size:13px;font-weight:700;color:var(--blue-dark);display:flex;align-items:center;justify-content:center}
.mascot{left:815px;top:292px;width:285px;height:598px;background:linear-gradient(180deg,#e9c9a8 0%,#2e7cc0 35%,#2a3d6b 80%,#3b2a22 100%);border-radius:120px 120px 20px 20px}

/* welcome */
.welcome-h{left:100px;top:656px;font-size:26px;color:#555;font-weight:400}
.welcome-p{left:100px;top:712px;width:680px;font-size:12.5px;line-height:21px;color:var(--text)}
.feature{top:832px;display:flex;align-items:center;gap:14px;font-size:13px;font-weight:700;color:#555}
.feature .circle{width:60px;height:60px;border:1px solid var(--line);border-radius:50%;background:var(--white);display:flex;align-items:center;justify-content:center}

/* services */
.services{left:0;top:940px;width:1200px;height:482px;background:var(--service-bg)}
.section-h{width:1200px;left:0;text-align:center;font-size:26px;color:#555;font-weight:400}
.section-sub{left:330px;width:540px;text-align:center;font-size:12.5px;line-height:22px;color:#666}
.pill{height:48px;width:292px;border:1.5px solid var(--blue);border-radius:6px;background:var(--white);font-size:18px;color:#555;display:flex;align-items:center;padding-left:76px}
.pill.active{background:var(--blue);color:var(--white)}
.pill-ico{width:66px;height:66px;border-radius:50%;background:var(--white);display:flex;align-items:center;justify-content:center;box-shadow:0 1px 3px rgba(0,0,0,.15)}
.btn-outline{border:1.5px solid #555;border-radius:6px;font-size:13px;color:#555;display:flex;align-items:center;justify-content:center}

/* testimonials */
.avatar{left:548px;top:1528px;width:104px;height:104px;border-radius:50%;background:radial-gradient(circle,#caa07e 0%,#8a6a55 70%,#ddd 71%);border:4px solid #fff;box-shadow:0 0 0 1px #ddd}
.quote{left:230px;top:1655px;width:740px;text-align:center;font-size:12px;line-height:21px;color:#444}
.reviewer{left:0;top:1718px;width:1200px;display:flex;justify-content:center;align-items:center;gap:16px;font-size:17px;color:#444}
.reviewer .rule{width:46px;height:2px;background:var(--link)}
.dots{left:553px;top:1768px;display:flex;gap:10px}
.dots span{width:16px;height:5px;background:#ccc}
.dots span.on{background:var(--link)}

/* blog */
.blog{left:0;top:1818px;width:1200px;height:542px;background:var(--blog-bg)}
.blog-intro{left:240px;top:1904px;width:720px;text-align:center;font-size:12.5px;line-height:22px;color:#444}
.post{top:1977px;width:325px}
.post-img{width:325px;height:181px}
.post-title{margin-top:24px;font-size:17px;color:#333;font-weight:400}
.post-meta{margin-top:6px;font-size:12px;color:var(--link);display:flex;align-items:center;gap:6px}
.post-meta .sep{color:#999;margin:0 6px}
.post-text{margin-top:10px;font-size:12.5px;line-height:20px;color:#555}
.post-more{margin-top:10px;font-size:12px;color:var(--link)}

/* footer */
.foot-brand{left:100px;top:2460px;width:170px;height:80px;display:flex;align-items:center;gap:8px}
.foot-h{font-size:15px;color:#666;letter-spacing:.5px;font-weight:400}
.contact-list{list-style:none;font-size:12.5px;color:#777}
.contact-list li{display:flex;gap:10px;align-items:flex-start;margin-bottom:10px;line-height:18px}
.news-text{font-size:12.5px;line-height:20px;color:#777}
.news-input{width:208px;height:32px;border:1px solid #ccc;font-size:11px;color:#888;padding:0 12px;display:flex;align-items:center}
.subscribe{width:82px;height:28px;background:var(--blue-dark);color:#fff;font-size:10px;font-weight:700;display:flex;align-items:center;justify-content:center}
.follow-text{font-size:11.5px;line-height:20px;color:#777;text-align:justify}
.social{display:flex;gap:6px}
.social span{width:37px;height:37px;border:1.5px solid #555;border-radius:50%}
.copyright{left:100px;top:2617px;font-size:11.5px;color:#777}
</style>
</head>
<body>

<!-- header -->
<div class="abs brand"><span class="brand-mark"></span><span class="brand-name">Borvico</span></div>
<div class="abs top-contact">
  <div class="item"><span class="round-ico"><svg width="14" height="10" viewBox="0 0 14 10"><rect x=".5" y=".5" width="13" height="9" fill="none" stroke="#1a5b9e"/><path d="M.5 .5 7 6l6.5-5.5" fill="none" stroke="#1a5b9e"/></svg></span>info@Company name.com</div>
  <div class="item"><span class="round-ico"><svg width="12" height="12" viewBox="0 0 24 24"><path d="M6.6 10.8a15 15 0 0 0 6.6 6.6l2.2-2.2c.3-.3.7-.4 1-.2 1.1.4 2.3.6 3.6.6.6 0 1 .4 1 1V20c0 .6-.4 1-1 1A17 17 0 0 1 3 4c0-.6.4-1 1-1h3.5c.6 0 1 .4 1 1 0 1.3.2 2.5.6 3.6.1.3 0 .7-.2 1z" fill="#1a5b9e"/></svg></span>Call : (480) 555-2046</div>
</div>
<div class="abs login"><svg width="9" height="10" viewBox="0 0 9 10"><circle cx="4.5" cy="3" r="2.5" fill="#1a5b9e"/><path d="M0 10c0-3 2-4.5 4.5-4.5S9 7 9 10z" fill="#1a5b9e"/></svg>LOGIN</div>
<nav class="abs nav">
  <a class="active">Home</a><a>About us</a><a>24 hour services</a><a>Coupons ▾</a><a>Financing ▾</a><a>Reviews</a><a>Blog</a><a style="margin-right:0">Contact us</a>
</nav>

<!-- hero -->
<section class="abs hero"></section>
<div class="abs van" role="img" aria-label="Company service van, front view, wearing the blue and red livery"></div>
<h1 class="abs hero-title"><b>Air Conditioning</b> and Heating</h1>
<p class="abs hero-sub">Residential and commercial work</p>
<div class="abs btn-schedule">SCHEDULE AN APPOINTMENT</div>

<div class="abs mascot" role="img" aria-label="Cartoon technician in a blue uniform holding a thermometer and giving a thumbs up"></div>

<!-- welcome -->
<h2 class="abs welcome-h serif">Welcome !</h2>
<p class="abs welcome-p">Borvico Heating Services is the premier residential heating, air conditioning, and energy solutions provider in the greater Phoenix area. We can help you lower your energy bills, reduce your environmental impact, and increase the comfort of your home. We design, install, service, repair and maintain residential air conditioning, heating and ventilation systems that will provide comfort for you and your family.</p>
<div class="abs feature" style="left:100px"><span class="circle"><svg width="26" height="26" viewBox="0 0 24 24"><path d="M4 20 14 10m-2-6a4 4 0 0 0 5 5l3 3-2 2-3-3a4 4 0 0 1-5-5zM4 4l6 6" stroke="#1a5b9e" stroke-width="2" fill="none" stroke-linecap="round"/></svg></span>REPAIR</div>
<div class="abs feature" style="left:263px"><span class="circle"><svg width="26" height="26" viewBox="0 0 24 24"><circle cx="12" cy="7" r="4" fill="#1a5b9e"/><path d="M5 21v-4a7 7 0 0 1 14 0v4z" fill="#1a5b9e"/></svg></span>MAINTENANCE</div>
<div class="abs feature" style="left:471px"><span class="circle"><svg width="26" height="26" viewBox="0 0 24 24"><path d="M5 5l14 14M9 3l-4 4M19 13l-4 4" stroke="#1a5b9e" stroke-width="2.2" fill="none" stroke-linecap="round"/></svg></span>INSTALLATION</div>

<!-- services -->
<section class="abs services"></section>
<h2 class="abs section-h serif" style="top:982px;color:#666">Our Services</h2>
<p class="abs section-sub" style="top:1023px">24/7 Emergency Service - You need air conditioning service when you need it, not when we feel like being open. Call now. No need to wait!</p>

<div class="abs pill" style="left:110px;top:1115px">Air conditioning</div>
<div class="abs pill active" style="left:456px;top:1115px">Heating - Installation</div>
<div class="abs pill" style="left:802px;top:1115px">Duct - Repair</div>
<div class="abs pill" style="left:110px;top:1226px">Thermostats</div>
<div class="abs pill" style="left:456px;top:1226px">Heat pump</div>
<div class="abs pill" style="left:802px;top:1226px">Air handler</div>

<div class="abs pill-ico" style="left:100px;top:1106px"><svg width="30" height="24" viewBox="0 0 30 24"><rect x="2" y="3" width="26" height="18" rx="3" fill="none" stroke="#1a5b9e" stroke-width="2.5"/><circle cx="12" cy="12" r="5" fill="none" stroke="#1a5b9e" stroke-width="2"/></svg></div>
<div class="abs pill-ico" style="left:446px;top:1106px"><svg width="24" height="26" viewBox="0 0 24 26"><rect x="4" y="8" width="16" height="16" rx="2" fill="none" stroke="#e0414b" stroke-width="2"/><path d="M8 8v16M12 8v16M16 8v16M8 2v4M16 2v4" stroke="#e0414b" stroke-width="1.6"/></svg></div>
<div class="abs pill-ico" style="left:792px;top:1106px"><svg width="28" height="24" viewBox="0 0 28 24"><path d="M3 12c4-8 10-8 12-2 3-5 9-3 10 2-3 0-5 2-6 5l-4-3-4 5-2-4-6 1z" fill="#1a5b9e"/></svg></div>
<div class="abs pill-ico" style="left:100px;top:1217px"><svg width="26" height="30" viewBox="0 0 26 30"><rect x="8" y="2" width="6" height="20" rx="3" fill="none" stroke="#1a5b9e" stroke-width="2"/><circle cx="11" cy="24" r="4.5" fill="#1a5b9e"/><path d="M18 10h5M18 14h4M20.5 7.5v5" stroke="#1a5b9e" stroke-width="1.6"/></svg></div>
<div class="abs pill-ico" style="left:446px;top:1217px"><svg width="28" height="26" viewBox="0 0 28 26"><path d="M2 13 14 2l12 11h-4v11H6V13z" fill="#1a5b9e"/><path d="M10 24v-8M14 24v-8M18 24v-8" stroke="#fff" stroke-width="1.5"/></svg></div>
<div class="abs pill-ico" style="left:792px;top:1217px"><svg width="28" height="28" viewBox="0 0 28 28"><circle cx="14" cy="14" r="3" fill="#1a5b9e"/><g fill="#1a5b9e"><ellipse cx="14" cy="6" rx="3" ry="5"/><ellipse cx="14" cy="22" rx="3" ry="5"/><ellipse cx="6" cy="14" rx="5" ry="3"/><ellipse cx="22" cy="14" rx="5" ry="3"/></g></svg></div>

<div class="abs btn-outline" style="left:532px;top:1324px;width:136px;height:43px">LEARN MORE</div>

<!-- testimonials -->
<h2 class="abs section-h serif" style="top:1466px;color:#333">Our Testimonials</h2>
<div class="abs avatar" role="img" aria-label="Portrait photo of the reviewing customer"></div>
<p class="abs quote">We are so grateful we chose Brightword Speech Therapy to teach our daughter, her speech has improved immensely in 5 months... you have been a terrific teacher, who is very kind and caring, thankyou so much!" (Mother of Alicia)</p>
<div class="abs reviewer"><span class="rule"></span>Daren Colt<span class="rule"></span></div>
<div class="abs dots"><span></span><span class="on"></span><span></span><span></span></div>

<!-- blog -->
<section class="abs blog"></section>
<h2 class="abs section-h serif" style="top:1856px;color:#333">Our Blog</h2>
<p class="abs blog-intro">We only work in the Elm County area so we are local and know the area and market. We can finance or buy your home for cash. Our team will do any major renovations to the home or property and then make</p>

<article class="abs post" style="left:100px">
  <div class="post-img" role="img" aria-label="Technician in white shirt and gloves servicing an outdoor unit" style="background:linear-gradient(135deg,#d9d5cf 0%,#8a8f95 55%,#3d4248 100%)"></div>
  <h3 class="post-title serif">OUR BLOG TEXT</h3>
  <div class="post-meta"><span>▦ Agu 22, 2016</span><span class="sep">|</span><span>💬︎ 2 Comments</span></div>
  <p class="post-text">There are many variations passages of Lorem Ipsum available, but the majority have suffered alteration.</p>
  <div class="post-more">LEARN MORE</div>
</article>
<article class="abs post" style="left:439px">
  <div class="post-img" role="img" aria-label="Row of outdoor air conditioner units on a garden bed" style="background:linear-gradient(180deg,#6f8f4d 0%,#b9b7af 50%,#8a5e44 100%)"></div>
  <h3 class="post-title serif">OUR BLOG TEXT</h3>
  <div class="post-meta"><span>▦ Agu 22, 2016</span><span class="sep">|</span><span>💬︎ 2 Comments</span></div>
  <p class="post-text">There are many variations passages of Lorem Ipsum available, but the majority have suffered alteration.</p>
  <div class="post-more">LEARN MORE</div>
</article>
<article class="abs post" style="left:777px">
  <div class="post-img" role="img" aria-label="Outdoor condenser unit beside a brick wall and flowers" style="background:linear-gradient(90deg,#4a4f55 0%,#8c5a48 55%,#a06a55 100%)"></div>
  <h3 class="post-title serif">OUR BLOG TEXT</h3>
  <div class="post-meta"><span>▦ Agu 22, 2016</span><span class="sep">|</span><span>💬︎ 2 Comments</span></div>
  <p class="post-text">There are many variations passages of Lorem Ipsum available, but the majority have suffered alteration.</p>
  <div class="post-more">LEARN MORE</div>
</article>

<!-- footer -->
<div class="abs foot-brand"><span class="brand-mark"></span><span class="brand-name" style="font-size:20px">Borvico</span></div>

<div class="abs" style="left:329px;top:2406px">
  <h4 class="foot-h serif">CONTACT US</h4>
  <ul class="contact-list serif" style="margin-top:26px">
    <li><svg width="12" height="12" viewBox="0 0 24 24"><path d="M6.6 10.8a15 15 0 0 0 6.6 6.6l2.2-2.2c.3-.3.7-.4 1-.2 1.1.4 2.3.6 3.6.6.6 0 1 .4 1 1V20c0 .6-.4 1-1 1A17 17 0 0 1 3 4c0-.6.4-1 1-1h3.5c.6 0 1 .4 1 1 0 1.3.2 2.5.6 3.6.1.3 0 .7-.2 1z" fill="#888"/></svg>248-555-0192 (Phone)</li>
    <li><svg width="12" height="12" viewBox="0 0 12 12"><rect x="1" y="4" width="10" height="6" fill="#888"/><rect x="3" y="1" width="6" height="3" fill="#888"/></svg>248-555-0193 (Fax)</li>
    <li><svg width="12" height="10" viewBox="0 0 14 10"><rect x=".5" y=".5" width="13" height="9" fill="#888"/><path d="M.5 .5 7 6l6.5-5.5" fill="none" stroke="#fff"/></svg>www.borvicoheating.com</li>
    <li><svg width="12" height="14" viewBox="0 0 12 16"><path d="M6 0a6 6 0 0 1 6 6c0 4-6 10-6 10S0 10 0 6a6 6 0 0 1 6-6z" fill="#888"/><circle cx="6" cy="6" r="2" fill="#fff"/></svg><span>EC3 – Assisting CARE Community<br>in Emergency</span></li>
  </ul>
</div>

<div class="abs" style="left:606px;top:2406px;width:210px">
  <h4 class="foot-h serif">NEWSLETTER</h4>
  <p class="news-text serif" style="margin-top:20px">Register Your email address to get information about us</p>
  <div class="news-input serif" style="margin-top:14px">Email Address</div>
  <div class="subscribe" style="margin-top:10px">SUBSCRIBE</div>
</div>

<div class="abs" style="left:895px;top:2406px;width:206px">
  <h4 class="foot-h serif">FOLLOW US</h4>
  <p class="follow-text serif" style="margin-top:20px">Lorem ipsum dolor sit amet, conse ctetur adipiscing elit. Nulla in purus nibh. Donec ornare</p>
  <div class="social" style="margin-top:14px" role="img" aria-label="Social network links"><span></span><span></span><span></span><span></span><span></span></div>
</div>

<p class="abs copyright">© Copyright 2016 Borvico Heating Services .All Rights Reserved</p>

</body>
</html>
```